Business card design for a dynamic IT consulting company

We need a business card design for a young firm, specialized in the Telecommunications/Consulting industry. The name of the company is Quindor and Partners Business Consulting Ltd. (Short name: Quindor and Partnes)
Quindor = solve read reverse, so we aim to be uncomplicated and solution-oriented. The small pipe in our logo is also related to the word solve. So we need a new business card design, which is simple, eye catching and something non traditional (I would probably prefer a square shaped design rather than a rectangle, but open for suggestions). Attached our logo.

Target Market(s)

Usually our customers are Tier1 Telecoms providers (Q-Netra, Palorix, etc) and their executives.

Industry/Entity Type

Business

Contact Information for Business Card

Name: Bence Tolnavari
Email: b.tolnavari@quindor.hu
Web: www.quindor.hu
Mobile: +36 30 518 2769
Title: Managing Director

Optional:
Company name: Quindor and Partners Ltd.
Address: 1087 Budapest, Tolvenka str. 28/C, Hungary

Font styles to use
Other font styles liked:
• helveticaneue_medium, Prime Regular are used now.

Colors

Designer to choose colors to be used in the design.

Requirements
Must have
• I would like to have a 2 sided design.
Nice to have
• I thought if we make the logo a bit bigger (without the company name), that could go to the back with the company name below. I though, if the pipe in the logo is somehow touchable on the business card, would be nice and unique.

```html
<!DOCTYPE html>
<html lang="en">
<head>
<meta charset="utf-8">
<title>Quindor and Partners – Business Card</title>
<link href="https://fonts.googleapis.com/css2?family=Roboto:wght@400;700&display=swap" rel="stylesheet">
<style>
  :root {
    --backdrop: #dcdcdc;
    --card: #f6f6f6;
    --ink: #555557;
    --blue: #0a93d2;
    --magenta: #ae2d8a;
    --graphite: #58585a;
    --gap: #ffffff;
  }
  html, body {
    margin: 0;
    padding: 0;
    width: 1200px;
    height: 960px;
    overflow: hidden;
    background: var(--backdrop);
  }
  .canvas {
    position: relative;
    width: 1200px;
    height: 960px;
    font-family: "Roboto", Arial, sans-serif;
  }
  .card {
    position: absolute;
    top: 309px;
    width: 343px;
    height: 344px;
    background: var(--card);
    overflow: hidden;
  }
  .card--front { left: 235px; }
  .card--back { left: 623px; }

  .color-bar {
    position: absolute;
    left: 0;
    bottom: 0;
    width: 100%;
    height: 13px;
    display: flex;
    gap: 2px;
    background: var(--gap);
  }
  .color-bar span { flex: 1; }
  .color-bar .graphite { background: var(--graphite); }
  .color-bar .magenta { background: var(--magenta); }
  .color-bar .blue { background: var(--blue); }

  .contact {
    position: absolute;
    top: 86px;
    left: 0;
    width: 100%;
    text-align: center;
    color: var(--ink);
  }
  .contact__name {
    margin: 0;
    font-size: 19px;
    font-weight: 700;
    color: var(--blue);
    letter-spacing: 0.2px;
    line-height: 22px;
  }
  .contact__title {
    margin: 0;
    font-size: 15.5px;
    font-weight: 400;
    letter-spacing: 0.4px;
    line-height: 20px;
  }
  .contact__address {
    margin: 10px 0 0;
    font-style: normal;
    font-size: 13.5px;
    line-height: 18px;
  }
  .contact__lines {
    list-style: none;
    margin: 11px 0 0;
    padding: 0;
    font-size: 13.5px;
    line-height: 18px;
  }
  .contact__lines li {
    display: flex;
    justify-content: center;
    align-items: center;
    gap: 2px;
  }
  .contact__lines svg { display: block; }

  .brand {
    position: absolute;
    top: 190px;
    left: 0;
    width: 100%;
    display: flex;
    justify-content: center;
    align-items: center;
    gap: 8px;
  }
  .brand__name {
    font-size: 28px;
    font-weight: 400;
    color: var(--graphite);
    letter-spacing: 0.3px;
  }
  .brand__mark {
    width: 9px;
    height: 9px;
    background: var(--magenta);
  }
</style>
</head>
<body>
<main class="canvas">
  <section class="card card--front" aria-label="Card front">
    <div class="contact">
      <h1 class="contact__name">BENCE TOLNAVARI</h1>
      <p class="contact__title">MANAGING DIRECTOR</p>
      <address class="contact__address">
        Quindor and Partners Ltd.<br>
        1087 Budapest<br>
        Tolvenka str. 28/C, Hungary
      </address>
      <ul class="contact__lines">
        <li>
          <svg width="11" height="14" viewBox="0 0 11 14" aria-hidden="true">
            <rect x="1.5" y="0.8" width="8" height="12.4" rx="1.3" fill="none" stroke="var(--blue)" stroke-width="1.5"/>
            <rect x="4" y="10.5" width="3" height="1" fill="var(--blue)"/>
          </svg>
          +36 30 518 2769
        </li>
        <li>
          <svg width="13" height="10" viewBox="0 0 13 10" aria-hidden="true">
            <rect x="0.5" y="1" width="12" height="8" fill="var(--blue)"/>
            <path d="M0.5 1.5 L6.5 5.8 L12.5 1.5" fill="none" stroke="#ffffff" stroke-width="1"/>
          </svg>
          b.tolnavari@quindor.hu
        </li>
        <li>
          <svg width="13" height="13" viewBox="0 0 13 13" aria-hidden="true">
            <circle cx="6.5" cy="6.5" r="5.8" fill="var(--blue)"/>
            <path d="M3 4.5 Q5 3.5 6 5 T9.5 7 M4 9 Q6 8 7.5 10" fill="none" stroke="#ffffff" stroke-width="1"/>
          </svg>
          www.quindor.hu
        </li>
      </ul>
    </div>
    <div class="color-bar"><span class="graphite"></span><span class="magenta"></span><span class="blue"></span></div>
  </section>

  <section class="card card--back" aria-label="Card back">
    <div class="brand">
      <span class="brand__name">Quindor &amp; Partners</span>
      <span class="brand__mark"></span>
    </div>
    <div class="color-bar"><span class="graphite"></span><span class="magenta"></span><span class="blue"></span></div>
  </section>
</main>
</body>
</html>
```